San Francisco Leading Consulting firm - 47Vora Web Design Project

•Create a Web Design
•Uncoded webpage layout design
•2 Pages Design - Homepage + Interior Page

Task Description
Hello, we're looking for a re-design our current website www.47vora-example.com

we have a sample mockup design @

http://47vora.pubtrellis-example.org/

This shows the layout that we like and also a sample of 6 pictures that would change based on where you mouse over..

6 pictures HOME design needs to be included.

SMART
THOUGHTFUL
FLEXIBLE
CREATIVE SERVICES
TECHNICAL SERVICES
PARTNERS

sites we like:

http://www.melvanadvisory-example.com/Home.cfm?id=Home
http://www.plinthworks-example.com/index.html

Our company can be best described as: 100+ employees, cutting-edge, depandable, innovative, strong, smart.

Our Primary focus is: IT Consulting Services and Creative Design services

47Vora LLC is a consulting firm providing creative design, business and technology solutions to both private and public interests.

Established in 1996, 47Vora is a San Francisco based company providing specialists for a range of business needs including:

Creative Design Services
•Print
•Logo Design
•Website Design
•Illustration

and

Business and Technology solutions

•Application Software and Web Development
•Business Process Re-Design (BPR)
•Business/Systems Analysis and Requirement Documentation
•Mentoring and Training
•Network/Hardware Installation Services
•System Design and Architecture
•Vendor Management
•Docuvault Architecture and Implementation

our sample mockup site:

Reason: Due to holiday season, we're not available to work with designers and finilize our design.  

Thank you very much for submitting your design.

We appreciate your time and creativity.   Since, our office is currently closed for holidays, we will be reviewing it in details next week and will make our decision as soon as possible.

It would be great if you could submit any of your changes by Wed next week, so it would be part of our reviews. 

Please see updated wireframe under attachments:  we have some minor updates to our wireframe that we would like you to update your designs, if possible.  

We also encorouge you not to use our standard wireframe and come up with more unique designs.   Everything would be considered when we review your design.

 

Target Market(s)

Creative services and professional services clients, including government agencies

Industry/Entity Type

Business

Requirements
Must have
• Clean, professional look, easy navigation

```html
<!DOCTYPE html>
<html lang="en">
<head>
<meta charset="utf-8">
<title>47Vora — Technology Solutions for the 21st Century</title>
<link href="https://fonts.googleapis.com/css2?family=Open+Sans:ital,wght@0,400;0,600;0,700;1,400&family=Arimo:wght@400;700&display=swap" rel="stylesheet">
<style>
:root{
  --header-bg:#eef6fb;
  --nav-bg:#dcedf6;
  --ink:#333;
  --ink-soft:#666;
  --muted:#888;
  --link:#1a7fc0;
  --cyan:#3ad2f2;
  --accent:#f0a020;
  --green:#6fd12e;
  --green-dark:#55c01c;
  --quote:#b5dff2;
  --line:#d8dde0;
  --card-bg:#fbfbfb;
}
*{box-sizing:border-box;margin:0;padding:0}
html,body{width:1159px;height:1200px;overflow:hidden}
body{position:relative;background:#f6f7f8;font-family:"Open Sans",sans-serif;color:var(--ink)}
.abs{position:absolute}

.site-header{left:0;top:0;width:1159px;height:100px;background:var(--header-bg)}
.brand{left:147px;top:40px;display:flex;align-items:center;gap:10px}
.brand-mark{width:26px;height:26px;border-radius:50%;background:#2a8fd0}
.brand-name{font-size:28px;font-weight:400;color:#3a4a55;letter-spacing:1px}
.tagline{left:333px;top:51px;font-size:12px;color:#444}
.contact{left:922px;top:16px;font-size:11.5px;color:var(--ink-soft);line-height:1.3}
.contact .value{color:var(--link);font-size:16px;margin-bottom:6px}
.contact .email{font-size:12.5px}

.main-nav{left:0;top:100px;width:1159px;height:37px;background:var(--nav-bg)}
.nav-item{top:12px;font-size:10.5px;font-weight:700;letter-spacing:.6px;color:#333;white-space:nowrap}
.nav-item .chev{color:var(--accent);margin-left:12px;font-weight:400}
.search{left:872px;top:8px;width:149px;height:21px;background:#fff;border:1px solid #cfdce4;border-radius:2px;font-size:8px;font-style:italic;color:#aaa;padding:5px 7px}
.search svg{position:absolute;right:5px;top:4px}

.welcome{left:0;top:137px;width:1159px;height:163px;background:#fff}
.welcome h1{position:absolute;left:152px;top:25px;font-weight:400;font-size:39px;color:var(--cyan);letter-spacing:-.5px}
.welcome p{position:absolute;left:152px;font-size:12px;color:#333;white-space:nowrap}
.welcome p.intro{letter-spacing:-.15px}

.slider-band{left:0;top:300px;width:1159px;height:311px;background:linear-gradient(#eceef0,#dfe2e5)}
.slider{left:137px;top:300px;width:880px;height:311px;overflow:hidden}
.slide-copy{left:0;top:0;width:291px;height:311px;background:linear-gradient(135deg,#86e040,var(--green-dark))}
.slide-copy h2{position:absolute;left:62px;top:130px;font-size:40px;font-weight:400;color:#fff}
.slide-copy p{position:absolute;left:65px;top:206px;font-size:19px;color:#fff;line-height:1.35}
.slide-photo{left:291px;top:0;width:393px;height:311px;background:linear-gradient(120deg,#c9cfd3,#e9ecee 45%,#8a8f93 70%,#d8dcdf)}
.slide-next{left:684px;top:0;width:150px;height:311px;border-left:2px solid var(--green);background:linear-gradient(160deg,#dbe8f5,#9ab6d6 50%,#dde8f3)}
.slide-edge{left:834px;top:0;width:46px;height:311px;background:var(--green)}
.arrow{top:140px}
.dots{left:18px;top:291px;display:flex;gap:5px}
.dots span{width:6px;height:6px;border-radius:50%;background:rgba(255,255,255,.5)}
.dots span.on{background:#fff}

.card{top:648px;width:257px;height:147px;background:var(--card-bg);border:1px solid #e6e8ea;border-radius:11px;box-shadow:0 2px 4px rgba(0,0,0,.06)}
.card svg{position:absolute;left:22px;top:38px}
.card h3{position:absolute;left:80px;font-size:17px;font-weight:400;color:#333;line-height:1.2;white-space:nowrap}
.card h3 small{display:block;font-size:17px;color:var(--muted)}
.card .more{position:absolute;right:18px;bottom:14px;font-size:11.5px;color:#333}
.card .more b{color:var(--accent);font-weight:400;margin-left:4px}

.clients{left:144px;top:865px;width:584px;height:84px;background:#fff;border:1px solid #d6dadd;border-radius:9px}
.clients span{position:absolute;left:15px;top:31px;font-size:15px;color:#666}
.clients svg{position:absolute;right:11px;top:33px}

.testimonial{left:760px;top:862px;width:236px}
.testimonial h4{font-size:15px;font-weight:400;color:#555}
.testimonial .quote-mark{color:var(--quote);font-size:34px;line-height:.7;height:16px;font-family:Georgia,serif}
.testimonial p{font-size:10.5px;font-style:italic;color:#888;line-height:1.3;margin-top:2px}
.testimonial .by{font-size:9.5px;color:#888;text-align:right;margin-top:5px}
.testimonial .end{text-align:right}

.services-index{left:96px;top:987px;width:917px;height:150px;font-family:"Arimo",sans-serif}
.services-index .divider{position:absolute;left:316px;top:0;width:1px;height:150px;background:var(--line)}
.services-index h5{position:absolute;top:9px;font-size:12.5px;font-weight:700;color:#333}
.services-index ul{position:absolute;top:35px;list-style:none;font-size:10px;color:var(--link)}
.services-index li{line-height:1.3;margin-bottom:12px;white-space:nowrap}
.services-index li::before{content:"• ";}
.services-index li .wrap{display:block;padding-left:9px}

.site-footer{left:96px;top:1150px;width:917px;height:50px;border-top:1px solid #e8eaec;text-align:center;font-family:"Arimo",sans-serif;font-size:10.5px;color:#222;padding-top:22px}
</style>
</head>
<body>

<header class="abs site-header">
  <div class="abs brand"><span class="brand-mark"></span><span class="brand-name">47Vora</span></div>
  <div class="abs tagline">Thechnology Solutions for the 21st Century</div>
  <div class="abs contact">
    <div>Call us at</div>
    <div class="value">800.555.014</div>
    <div>Email us at</div>
    <div class="value email">info@47vora-example.com</div>
  </div>
</header>

<nav class="abs main-nav">
  <span class="abs nav-item" style="left:151px">COMPANY<span class="chev">›</span></span>
  <span class="abs nav-item" style="left:249px">CREATIVE SERVICES<span class="chev">›</span></span>
  <span class="abs nav-item" style="left:407px">TECHNICAL SERVICES<span class="chev">›</span></span>
  <span class="abs nav-item" style="left:584px">PARTNERS<span class="chev">›</span></span>
  <span class="abs nav-item" style="left:695px">CONTACT US</span>
  <div class="abs search">SEARCH
    <svg width="12" height="12" viewBox="0 0 12 12"><circle cx="7" cy="5" r="3.5" fill="none" stroke="#f0a020" stroke-width="1.5"/><line x1="4.5" y1="7.5" x2="1.5" y2="10.5" stroke="#f0a020" stroke-width="1.8"/></svg>
  </div>
</nav>

<section class="abs welcome">
  <h1>welcome</h1>
  <p style="top:90px">47Vora LLC is a consulting firm providing creative design, business and technology solutions to both private and public interests.</p>
  <p class="intro" style="top:120px">Our experts possess broad industry knowledge which can help with technical and business process challenges, delivering solutions that are creative and cost effective.</p>
</section>

<div class="abs slider-band"></div>
<section class="abs slider">
  <div class="abs slide-copy">
    <h2>flexible</h2>
    <p>the world moves too<br>fast for rigid solutions</p>
    <svg class="abs arrow" style="left:14px" width="16" height="34" viewBox="0 0 16 34"><polyline points="14,2 2,17 14,32" fill="none" stroke="#fff" stroke-width="2"/></svg>
    <div class="abs dots"><span></span><span></span><span class="on"></span><span></span><span></span><span></span></div>
  </div>
  <div class="abs slide-photo" role="img" aria-label="Photo of a young man sitting on the floor of a bright office working on a laptop"></div>
  <div class="abs slide-next" role="img" aria-label="Close-up photo of a blue coiled spring toy"></div>
  <div class="abs slide-edge">
    <svg class="abs arrow" style="left:15px" width="16" height="34" viewBox="0 0 16 34"><polyline points="2,2 14,17 2,32" fill="none" stroke="#fff" stroke-width="2"/></svg>
  </div>
</section>

<article class="abs card" style="left:144px">
  <svg width="44" height="50" viewBox="0 0 44 50"><polygon points="4,46 40,46 4,10" fill="none" stroke="#1a8fd0" stroke-width="4"/><line x1="14" y1="36" x2="38" y2="4" stroke="#1a8fd0" stroke-width="6"/></svg>
  <h3 style="top:46px">Creative<small>Services</small></h3>
  <span class="more">Lean More<b>›</b></span>
</article>
<article class="abs card" style="left:449px">
  <svg width="44" height="50" viewBox="0 0 44 50"><line x1="6" y1="42" x2="30" y2="14" stroke="#a03a45" stroke-width="6"/><circle cx="32" cy="11" r="7" fill="none" stroke="#a03a45" stroke-width="4"/><line x1="34" y1="46" x2="34" y2="28" stroke="#a03a45" stroke-width="4"/><polyline points="27,34 34,26 41,34" fill="none" stroke="#a03a45" stroke-width="4"/></svg>
  <h3 style="top:44px">Business &amp; Technical<small>Services</small></h3>
  <span class="more">Lean More<b>›</b></span>
</article>
<article class="abs card" style="left:753px">
  <svg width="50" height="50" viewBox="0 0 50 50"><rect x="4" y="14" width="16" height="14" fill="#8eae2a"/><rect x="30" y="14" width="16" height="14" fill="#8eae2a"/><line x1="14" y1="36" x2="36" y2="20" stroke="#8eae2a" stroke-width="8"/></svg>
  <h3 style="top:60px">Partners</h3>
  <span class="more">Lean More<b>›</b></span>
</article>

<section class="abs clients">
  <span>Our Clinets</span>
  <svg width="10" height="16" viewBox="0 0 10 16"><polyline points="2,2 8,8 2,14" fill="none" stroke="#777" stroke-width="2"/></svg>
</section>

<aside class="abs testimonial">
  <h4>Testimonials</h4>
  <div class="quote-mark">“</div>
  <p>Lorem ipsum dolor sit amet, consectetuer adipiscing elit, sed diam nonummy nibh euismod.</p>
  <div class="by">Dana Mercer, CEO of Company</div>
  <div class="quote-mark end">”</div>
</aside>

<section class="abs services-index">
  <h5 style="left:50px">Creative Design Services</h5>
  <ul style="left:64px">
    <li>Print</li><li>Logo Design</li><li>Website Design</li><li>Illustration</li>
  </ul>
  <div class="divider"></div>
  <h5 style="left:363px">Business and Technical solutions</h5>
  <ul style="left:377px">
    <li>Application Software and Web Development</li>
    <li>Business Process Re-Design (BPR)</li>
    <li>Business/Systems Analysis and Requirement<span class="wrap">Documentation</span></li>
    <li>Mentoring and Training</li>
  </ul>
  <ul style="left:636px">
    <li>Network/Hardware Installation Services</li>
    <li>System Design and Architecture</li>
    <li>Vendor Management</li>
    <li>Docuvault Architecture and Implementation</li>
  </ul>
</section>

<footer class="abs site-footer">Copyright 2010, 47Vora, LLC All rights reserved.</footer>

</body>
</html>
```